Web Design for guards MMJ transport and security services

Harbor Crest Protective solutions a tallow unified company, is looking for a designer to create a website that displays our service portfolio. We need marketing pictures and content to be created in a original and competitive fashion, intriguing to our customers. We will need forms on the website to be created for calendar booking (somehow integrate into exchange if possible) and general inquiry forms. There will need to be pages dedicated to our staff, MMJ trasnport & Courier services, our vehicles, alarm systems, video systems, video monitoring, private investigations, and surveillance aduit and compliance investigations, payment gateway integration, and general company information. I Have attached our main company logo. Also have a emphasis on being state licensed by the Colorado RPB. Have a link to our parent site, tallowcctv.example

Target Market(s)

Colorado Marijuana industry, MMJ transport services, guard services, armed gaurd services.

Contact Information for Business Card

Would like a sleek simple design highlighting what we offer. must match the website and have a overall professional straight to the point appearance.

Number of Pages Required

1 page

Colors
33b8a4
00a990
9bcb3c
acd036
cadf82
85cae6
33a6d7
0792cd

Requirements
Must have
• Easy to use, lots of images, professional.
Nice to have
• Creativity

```html
<!DOCTYPE html>
<html lang="en">
<head>
<meta charset="utf-8">
<title>Harbor Crest Protective Solutions</title>
<link rel="stylesheet" href="https://fonts.googleapis.com/css2?family=Roboto:wght@300;400;500;700&family=Open+Sans:ital,wght@0,400;0,600;0,700;1,400&display=swap">
<style>
:root{
  --red:#d7151f;
  --red-dark:#b70f18;
  --teal:#19a990;
  --green:#8cc63e;
  --blue:#1b95d3;
  --ink:#2b2f33;
  --muted:#8a8f94;
  --panel:#232a30;
  --footer:#14181c;
  --footer-bar:#0d1013;
  --soft:#f4f5f7;
  --white:#ffffff;
}
*{box-sizing:border-box;margin:0;padding:0}
html,body{width:1200px;height:2848px;overflow:hidden;background:var(--white)}
body{position:relative;font-family:"Open Sans",Arial,sans-serif;color:var(--ink)}
a{color:inherit;text-decoration:none}

/* header */
.site-header{position:absolute;left:0;top:0;width:1200px;height:127px;background:var(--white)}
.brand{position:absolute;left:100px;top:22px;display:flex;align-items:center;gap:10px}
.brand-dot{width:34px;height:34px;border-radius:50%;background:var(--red)}
.brand-name{font-family:"Roboto",sans-serif;font-weight:700;font-size:20px;color:var(--red)}
.utility-nav{position:absolute;right:60px;top:26px;font-size:11px;color:#a3a7ab;font-family:"Roboto",sans-serif}
.utility-nav span{margin:0 8px;color:#ccc}
.main-nav{position:absolute;left:304px;top:63px;width:896px;height:64px;background:var(--red);clip-path:polygon(28px 0,100% 0,100% 100%,0 100%)}
.main-nav ul{list-style:none;display:flex;height:100%;align-items:center;padding-left:14px;font-family:"Roboto",sans-serif;font-size:14px;color:var(--white)}
.main-nav li{padding:0 15px;height:100%;display:flex;align-items:center}
.main-nav li.active{background:var(--red-dark);margin-left:6px;padding:0 20px}

/* hero */
.hero{position:absolute;left:0;top:127px;width:1200px;height:560px;overflow:hidden}
.hero-photo{position:absolute;inset:0;background:linear-gradient(90deg,#bfc4c8 0%,#9da4aa 45%,#c9ced2 100%)}
.hero-guard{position:absolute;right:0;top:0;width:330px;height:520px;background:linear-gradient(180deg,#8e9aa6,#5d6a76)}
.hero-caption{position:absolute;left:70px;top:143px;width:593px;height:186px;background:rgba(38,40,44,.88);padding:34px 0 0 50px;color:var(--white)}
.hero-caption h1{font-family:"Open Sans",sans-serif;font-weight:600;font-size:48px;line-height:1.05;letter-spacing:1px}
.hero-caption p{font-family:"Open Sans",sans-serif;font-weight:300;font-size:36px;margin-top:6px;letter-spacing:.5px}
.hero-curve{position:absolute;left:0;top:127px;width:1200px;height:560px;pointer-events:none}

/* section titles */
.section-title{position:absolute;left:0;width:1200px;text-align:center;font-family:"Roboto",sans-serif;font-weight:300;font-size:26px;color:#333;letter-spacing:.5px}
.section-title::after{content:"";display:block;width:56px;height:2px;background:var(--red);margin:12px auto 0}

/* services */
.service-card{position:absolute;width:484px;height:122px;color:var(--white);padding:22px 26px 0 28px}
.service-card .frame{position:absolute;right:-6px;bottom:-6px;width:210px;height:40px;border-right:1px solid var(--frame);border-bottom:1px solid var(--frame)}
.service-card .frame-tl{position:absolute;left:-6px;top:-6px;width:50px;height:30px;border-left:1px solid var(--frame);border-top:1px solid var(--frame)}
.card-teal{background:var(--teal);--frame:var(--teal)}
.card-green{background:var(--green);--frame:var(--green)}
.card-red{background:var(--red);--frame:var(--red)}
.card-blue{background:var(--blue);--frame:var(--blue)}
.service-head{display:flex;align-items:center;gap:14px;font-family:"Roboto",sans-serif;font-weight:500;font-size:17px;text-transform:uppercase}
.service-head svg{width:32px;height:28px;flex:none}
.service-card p{font-size:11px;line-height:19px;margin-top:14px;opacity:.95;letter-spacing:-.1px}

/* about */
.about{position:absolute;left:0;top:1134px;width:1200px;height:470px}
.about-photo{position:absolute;left:0;top:0;width:598px;height:470px;background:linear-gradient(180deg,#2d4f6c 0%,#c9823a 50%,#f2b548 62%,#6a3a22 100%)}
.about-panel{position:absolute;left:598px;top:0;width:602px;height:470px;background:var(--panel);padding:74px 60px 0 57px;color:var(--white)}
.about-panel h2{font-family:"Roboto",sans-serif;font-weight:300;font-size:27px}
.about-panel h3{font-family:"Roboto",sans-serif;font-weight:500;font-size:16px;margin-top:38px;letter-spacing:.3px}
.about-panel .lead{font-size:12px;line-height:22px;color:#7d858c;margin-top:16px;text-align:justify}
.checks{list-style:none;margin-top:24px;font-family:"Roboto",sans-serif;font-weight:500;font-size:13px}
.checks li{display:flex;align-items:center;gap:16px;height:27px}
.checks svg{width:14px;height:12px}
.license-badge{position:absolute;left:328px;top:290px;width:130px;height:130px;border-radius:50%;background:#0f0f10;border:6px solid #b88a2e}

/* news */
.news-card{position:absolute;width:488px;height:160px;background:var(--white);box-shadow:0 2px 10px rgba(0,0,0,.12)}
.news-thumb{position:absolute;left:0;top:10px;width:158px;height:140px;background:linear-gradient(135deg,#7e8e9c,#c7ced4)}
.news-thumb.t2{background:linear-gradient(135deg,#4e6070,#a4b2bd)}
.news-thumb.t3{background:linear-gradient(135deg,#8aa2b8,#d4d9dd)}
.news-thumb.t4{background:linear-gradient(135deg,#c4c8cb,#8e9297)}
.news-body{position:absolute;left:173px;top:18px;right:22px}
.news-body h4{font-family:"Roboto",sans-serif;font-weight:500;font-size:16px;color:#333;letter-spacing:.3px}
.news-body h4.hot{color:var(--red)}
.news-body p{font-size:11.5px;line-height:20px;color:#777;margin-top:10px;text-align:justify}
.read-more{position:absolute;right:22px;bottom:16px;font-size:12px;color:#555}
.read-more.hot{color:var(--red)}

/* testimonial */
.testimonial{position:absolute;left:0;top:2142px;width:1200px;height:406px;background:var(--soft)}
.avatar{position:absolute;left:556px;top:128px;width:88px;height:88px;border-radius:50%;background:linear-gradient(180deg,#d9b49a,#a7805f);border:4px solid #e4e6e8;box-shadow:0 0 0 1px #c8ccd0}
.person-name{position:absolute;left:0;top:234px;width:1200px;text-align:center;font-family:"Roboto",sans-serif;font-weight:500;font-size:17px;line-height:22px;color:#333}
.person-role{position:absolute;left:0;top:258px;width:1200px;text-align:center;font-style:italic;font-size:13px;line-height:18px;color:#888}
.quote{position:absolute;left:280px;top:286px;width:640px;text-align:center;font-size:12px;line-height:21px;color:#666}
.quote strong{display:block;color:#444;font-weight:600}
.slider-arrow{position:absolute;top:182px;width:26px;height:56px}

/* footer */
.site-footer{position:absolute;left:0;top:2548px;width:1200px;height:300px;background:var(--footer);color:var(--white)}
.footer-brand{position:absolute;left:99px;top:95px;display:flex;align-items:center;gap:12px}
.footer-brand .mark{width:46px;height:46px;border-radius:50%;background:var(--blue)}
.footer-brand .word{font-family:"Roboto",sans-serif;font-weight:500;font-size:26px;color:#2fa2dc;letter-spacing:1px}
.footer-col{position:absolute;top:58px}
.footer-col h5{font-family:"Roboto",sans-serif;font-weight:500;font-size:15px;margin-bottom:14px}
.footer-col li{list-style:none;font-size:12px;color:#a9afb5;line-height:24px}
.footer-bar{position:absolute;left:0;top:243px;width:1200px;height:57px}
.copyright{position:absolute;left:99px;top:20px;font-size:11px;color:#8f969c}
.legal{position:absolute;left:500px;top:0;width:700px;height:57px;background:var(--footer-bar);clip-path:polygon(40px 0,100% 0,100% 100%,0 100%);display:flex;align-items:center;padding-left:72px;font-size:11px;color:#a9afb5}
.legal span.sep{margin:0 18px;color:#666}
.socials{position:absolute;left:948px;top:15px;display:flex;gap:10px}
.socials i{display:block;width:26px;height:26px;border-radius:50%;border:1px solid #6b7177}
</style>
</head>
<body>

<header class="site-header">
  <div class="brand"><span class="brand-dot"></span><span class="brand-name">Harbor Crest</span></div>
  <nav class="utility-nav">About us<span>|</span>MMJ Trasnport &amp; Courier services<span>|</span>Our vehicles<span>|</span>Alarm systems<span>|</span>video systems</nav>
  <nav class="main-nav">
    <ul>
      <li class="active">Home</li><li>About us</li><li>Our staff</li><li>private investigations</li><li>Surveillance audit</li><li>Compliance investigations</li><li>Contact us</li>
    </ul>
  </nav>
</header>

<section class="hero">
  <div class="hero-photo" role="img" aria-label="Blurred harbor and cargo port backdrop"></div>
  <div class="hero-guard" role="img" aria-label="Uniformed security guard seen from behind"></div>
  <div class="hero-caption">
    <h1>HARBOR CREST</h1>
    <p>PROTECTIVE SOLUTIONS.</p>
  </div>
</section>
<svg class="hero-curve" viewBox="0 0 1200 560" aria-hidden="true">
  <path d="M0 452 L600 543 L1200 443 L1200 560 L0 560 Z" fill="#fff"/>
  <path d="M0 452 L600 543 L1200 443" fill="none" stroke="#d7151f" stroke-width="2"/>
  <path d="M548 543 A52 52 0 0 1 652 543 Z" fill="#fff"/>
  <path d="M590 512 l-8 9 l8 9 M610 512 l8 9 l-8 9" fill="none" stroke="#333" stroke-width="2"/>
</svg>

<h2 class="section-title" style="top:722px">OUR SERVICE</h2>

<article class="service-card card-teal" style="left:104px;top:797px">
  <span class="frame-tl"></span><span class="frame"></span>
  <div class="service-head"><svg viewBox="0 0 32 28"><path d="M2 7h17v13H2z M19 11h6l5 5v4H19z" fill="#fff"/><circle cx="8" cy="22" r="3" fill="#fff"/><circle cx="25" cy="22" r="3" fill="#fff"/></svg>Easy Transport</div>
  <p>But I must explain to you how all this mistaken idea of denouncing pleasure and praising pain was born and I will give you a complete account of the system</p>
</article>
<article class="service-card card-green" style="left:613px;top:797px">
  <span class="frame-tl"></span><span class="frame"></span>
  <div class="service-head"><svg viewBox="0 0 32 28"><path d="M16 1 L28 5 V13 C28 20 22 25 16 27 C10 25 4 20 4 13 V5 Z" fill="#fff"/><path d="M11 14 l4 4 l7 -8" fill="none" stroke="#8cc63e" stroke-width="2.5"/></svg>Security Services</div>
  <p>But I must explain to you how all this mistaken idea of denouncing pleasure and praising pain was born and I will give you a complete account of the system</p>
</article>
<article class="service-card card-red" style="left:104px;top:947px">
  <span class="frame-tl"></span><span class="frame"></span>
  <div class="service-head"><svg viewBox="0 0 32 28"><path d="M9 8h14l-2-6h-10z" fill="#fff"/><circle cx="16" cy="13" r="5" fill="#fff"/><path d="M6 27c0-6 4-9 10-9s10 3 10 9z" fill="#fff"/></svg>Compliance Investigations</div>
  <p>But I must explain to you how all this mistaken idea of denouncing pleasure and praising pain was born and I will give you a complete account of the system</p>
</article>
<article class="service-card card-blue" style="left:613px;top:947px">
  <span class="frame-tl"></span><span class="frame"></span>
  <div class="service-head"><svg viewBox="0 0 32 28"><path d="M3 9 L16 3 L29 9 L16 15 Z M3 11 L15 17 V27 L3 21 Z M29 11 L17 17 V27 L29 21 Z" fill="#fff"/></svg>Courier Services</div>
  <p>But I must explain to you how all this mistaken idea of denouncing pleasure and praising pain was born and I will give you a complete account of the system</p>
</article>

<section class="about">
  <div class="about-photo" role="img" aria-label="Cargo ship, container cranes and airplane at sunset"></div>
  <div class="about-panel">
    <h2>ABOUT US</h2>
    <h3>HARBOR CREST PROTECTIVE SOLUTIONS.</h3>
    <p class="lead">Sed ut perspiciatis unde omnis iste natus error sit voluptatem accusantium doloremque laudantium, totam rem aperiam, eaque ipsa quae ab illo inventore veritatis et quasi architecto beatae vitae dicta sunt explicabo. Nemo enim ipsam voluptatem quia voluptas sit aspernatur aut odit aut fugit, sed quia consequuntur magni dolores eos qui ratione voluptatem sequi nesciunt</p>
    <ul class="checks">
      <li><svg viewBox="0 0 14 12"><path d="M1 6 l4 4 l8 -9" fill="none" stroke="#2fa2dc" stroke-width="2.5"/></svg>Neque porro quisquam est, qui</li>
      <li><svg viewBox="0 0 14 12"><path d="M1 6 l4 4 l8 -9" fill="none" stroke="#2fa2dc" stroke-width="2.5"/></svg>Neque porro quisquam est, qui</li>
      <li><svg viewBox="0 0 14 12"><path d="M1 6 l4 4 l8 -9" fill="none" stroke="#2fa2dc" stroke-width="2.5"/></svg>Neque porro quisquam est, qui</li>
    </ul>
    <div class="license-badge" role="img" aria-label="State license badge"></div>
  </div>
</section>

<h2 class="section-title" style="top:1642px">LATEST NEWS</h2>

<article class="news-card" style="left:99px;top:1728px">
  <div class="news-thumb" role="img" aria-label="Guard reviewing paperwork"></div>
  <div class="news-body"><h4 class="hot">FINIBUS BONORUM MALORUM</h4><p>Portal Consulting Training programs are perfect for individuals to enhance their careers. Our hands-on practical and interactive programs use real time</p></div>
  <a class="read-more hot">[ Read More ]</a>
</article>
<article class="news-card" style="left:613px;top:1728px">
  <div class="news-thumb t2" role="img" aria-label="Travellers with luggage"></div>
  <div class="news-body"><h4>FINIBUS BONORUM MALORUM</h4><p>Our Offshore development model has a unique distinction of providing efficient software solutions with cost and quality advantage, using state-of-the-art</p></div>
  <a class="read-more">[ Read More ]</a>
</article>
<article class="news-card" style="left:99px;top:1931px">
  <div class="news-thumb t3" role="img" aria-label="Transport van on a city street"></div>
  <div class="news-body"><h4>FINIBUS BONORUM MALORUM</h4><p>Drawing on our experience in all major industries, we develop solutions that meet the most challenging IT problems. Our team follows</p></div>
  <a class="read-more">[ Read More ]</a>
</article>
<article class="news-card" style="left:613px;top:1931px">
  <div class="news-thumb t4" role="img" aria-label="Hands holding a small airplane model"></div>
  <div class="news-body"><h4>FINIBUS BONORUM MALORUM</h4><p>As organizations work to achieve and sustain competitive advantage, the ability for IT departments to demonstrate their value and deliver results</p></div>
  <a class="read-more">[ Read More ]</a>
</article>

<section class="testimonial">
  <h2 class="section-title" style="top:38px">OUR TESTIMONIAL</h2>
  <svg class="slider-arrow" style="left:34px" viewBox="0 0 26 56" aria-hidden="true"><path d="M22 2 L4 28 L22 54" fill="none" stroke="#b5bbc0" stroke-width="1.5"/></svg>
  <svg class="slider-arrow" style="right:34px" viewBox="0 0 26 56" aria-hidden="true"><path d="M4 2 L22 28 L4 54" fill="none" stroke="#b5bbc0" stroke-width="1.5"/></svg>
  <div class="avatar" role="img" aria-label="Client portrait"></div>
  <p class="person-name">Dana Whitfield</p>
  <p class="person-role">Front end developer</p>
  <p class="quote">Well, ever since we started coming here they have given us such great service.&nbsp; I am beyond happy with all of the work that has been done to me, I loved it. That is something the other dentists were never able to do for me.<strong>Thank you so much!</strong></p>
</section>

<footer class="site-footer">
  <div class="footer-brand"><span class="mark"></span><span class="word">TALLOW UNIFIED</span></div>
  <div class="footer-col" style="left:413px"><h5>ABOUT US</h5><ul><li>Home</li><li>About Us</li><li>Our Staff</li><li>Mmj Trasnport</li><li>Courier Services</li></ul></div>
  <div class="footer-col" style="left:585px"><h5>PRODUCT</h5><ul><li>Our Vehicles</li><li>Alarm Systems</li><li>Video Systems</li><li>Video Monitoring</li></ul></div>
  <div class="footer-col" style="left:746px"><h5>QUICK LINKS</h5><ul><li>Private Investigations</li><li>Surveillance Audit</li><li>Compliance Investigations</li><li>Contact Us</li></ul></div>
  <div class="footer-col" style="left:948px"><h5>CONTACT US</h5><ul><li>help@harborcrest.example</li><li>(000) - 555 0142</li><li>Social , Updates</li></ul></div>
  <div class="footer-bar">
    <p class="copyright">Copyrights@2016Company name @all rights reserved</p>
    <div class="legal">Privacy Policy<span class="sep">\</span>Terms &amp; Conditions<span class="sep">\</span>Sitemap</div>
    <div class="socials"><i></i><i></i><i></i><i></i></div>
  </div>
</footer>

</body>
</html>
```